Business Card Design For A Cajun Seafood Restaurant

We are opening a cajun seafood restaurant in a week. We mainly serve cajun seafood which is orginally from Louisiana. We want design on both sides of a business card. I have menu on the website. You can go to www.reednkettle.example to check out our menu.

Restaurant name: Reed N' Kettle
Phone: +1 (555) 304-7712
Address: 48206 Ludlow Row, #7, Bexmoor Flats, Ca90000
Email: reednkettle@mailbox.example
Website: www.reednkettle.example

Maybe add social media icons (facebook, instagram) if looks nice on the business card.
facebook.com/reednkettle
instagram.com/reednkettle or @reednkettle

Attached is the logo and other business card samples that I like.

```html
<!DOCTYPE html>
<html lang="en">
<head>
<meta charset="utf-8">
<title>Reed N' Kettle – Business Card</title>
<link rel="stylesheet" href="https://fonts.googleapis.com/css2?family=Source+Sans+3:wght@400;600&display=swap">
<style>
  :root {
    --stage: #000000;
    --olive: #7a6417;
    --gold: #dab21b;
    --gold-deep: #c99c14;
    --accent: #f2c200;
    --ink: #1a1a1a;
    --paper: #ffffff;
    --rule: #e9dfb8;
  }
  * { box-sizing: border-box; margin: 0; padding: 0; }
  html, body { width: 1200px; height: 900px; overflow: hidden; background: var(--stage); }
  .canvas { position: relative; width: 1200px; height: 900px; font-family: "Source Sans 3", sans-serif; }

  .card { position: absolute; top: 275px; width: 477px; height: 293px; overflow: hidden; }
  .card-front { left: 116px; background: var(--olive); border-radius: 0 46px 0 46px; }
  .card-back  { left: 622px; background: var(--gold); border-radius: 46px 0 46px 0; }

  .mascot { position: absolute; border-radius: 50%; }
  .card-front .mascot { left: 296px; top: 22px; width: 150px; height: 140px;
    background: radial-gradient(circle at 50% 45%, #f0c12a 0%, #e8761f 55%, rgba(232,118,31,0) 72%); }
  .card-back .mascot { left: 186px; top: 56px; width: 114px; height: 104px;
    background: radial-gradient(circle at 50% 45%, #f0c12a 0%, #e8761f 55%, rgba(232,118,31,0) 72%); }

  .brand-name { position: absolute; font-family: "Source Sans 3", sans-serif; font-weight: 600; font-style: normal; white-space: nowrap; }
  .card-front .brand-name { left: 24px; top: 131px; font-size: 23px; line-height: 28px; color: var(--accent); }

  .divider { position: absolute; left: 0; top: 169px; width: 100%; height: 1.5px; background: var(--rule); }

  .address { position: absolute; left: 24px; top: 184px; color: var(--paper); font-size: 13.5px; line-height: 19px; font-style: normal; }

  .contacts { position: absolute; right: 24px; top: 184px; list-style: none; color: var(--paper); font-size: 13.5px; line-height: 18.5px; text-align: right; }
  .contacts li { display: flex; justify-content: flex-end; align-items: center; gap: 7px; }
  .contacts svg { width: 10px; height: 10px; fill: var(--accent); }

  .social { position: absolute; right: 24px; top: 248px; display: flex; align-items: center; gap: 8px; color: var(--paper); font-size: 16px; font-weight: 600; }
  .social .dot { width: 14px; height: 14px; border-radius: 3px; background: var(--accent); }
  .social .handle { margin-left: 12px; }

  .pattern-field { position: absolute; inset: 0; background: linear-gradient(180deg, var(--gold) 0%, var(--gold-deep) 100%); }

  .card-back .brand-name { left: 0; right: 0; top: 158px; text-align: center; font-size: 22px; line-height: 26px; color: var(--ink); }
  .tagline { position: absolute; left: 0; right: 0; top: 187px; text-align: center; font-size: 11.5px; font-weight: 600; letter-spacing: 1px; color: var(--ink); text-transform: uppercase; }
</style>
</head>
<body>
<main class="canvas">

  <section class="card card-front" aria-label="Card front">
    <div class="mascot" role="img" aria-label="Illustrated restaurant mascot holding corn"></div>
    <p class="brand-name">Reed N' Kettle</p>
    <div class="divider"></div>
    <address class="address">48206 Ludlow Row,<br>#7, Bexmoor Flats, Ca90000</address>
    <ul class="contacts">
      <li>+1 (555) 304-7712
        <svg viewBox="0 0 10 10" aria-hidden="true"><path d="M2 0.5 L3.6 2.6 L2.7 3.6 Q3.8 5.8 6.4 7.3 L7.4 6.4 L9.5 8 L8.3 9.5 Q3.6 8.6 0.5 1.7 Z"/></svg></li>
      <li>reednkettle@mailbox.example
        <svg viewBox="0 0 10 10" aria-hidden="true"><path d="M0.5 2 H9.5 V8 H0.5 Z M1.2 2.6 L5 5.4 L8.8 2.6 Z" fill-rule="evenodd"/></svg></li>
      <li>www.reednkettle.example
        <svg viewBox="0 0 10 10" aria-hidden="true"><circle cx="5" cy="5" r="4.5"/></svg></li>
    </ul>
    <div class="social">
      <span class="dot" aria-hidden="true"></span>
      <span class="dot" aria-hidden="true"></span>
      <span class="handle">/reednkettle</span>
    </div>
  </section>

  <section class="card card-back" aria-label="Card back">
    <div class="pattern-field" role="img" aria-label="Faint repeating mascot pattern on yellow"></div>
    <div class="mascot" role="img" aria-label="Illustrated restaurant mascot holding corn"></div>
    <p class="brand-name">Reed N' Kettle</p>
    <p class="tagline">Cajun Seafood House</p>
  </section>

</main>
</body>
</html>
```